Brightline Energy Product Distribution Brochure

We are looking to have our current brochure for our customers completely redesigned...the idea is to present the relevant information in an attractive way . Our website is brightlineenergyco.example where you can find more information about us. We have included a file with a rough idea of the page order and what each should include but feel free to adapt based on design. The example provided is only for context and doesnt have to be maintained. We will be using the brochure both digitally and in print form. As long as it reads easily and is eye catching, the design can be horizontal or vertical.Final deliverable should be indesign file.

"Our Brands" page: should be limited to one page (space being enough) where it has the header for each one (for example diesel generators) space for one or two lines of text and then the corresponding logos for each of the five categories
Updates

For those asking: the "our brands" page should be a single page layout where there is a header with the corresponding section and space for maybe one line of text followed by the two logos for that category. Each of the product pages should be similar in fashion to the one in the document attached: a photo of the product with some white space and space for the text to be included. We will be posting additional examples today

Target Market(s)

We want to present it to customers both digitally and in print so they can see our products

Industry/Entity Type

Power Generation

Font styles to use
Serif

Requirements
Must have
• Eye catching and able to present the information in a presentable fashion. Rest is up to you.
Nice to have
• Should incorporate the colors of our logo but can also add other depending on design

```html
<!DOCTYPE html>
<html lang="en">
<head>
<meta charset="utf-8">
<title>Brightline Energy – Brochure Spreads</title>
<link rel="stylesheet" href="https://fonts.googleapis.com/css2?family=Barlow:ital,wght@0,400;0,600;0,700;1,300;1,700&display=swap">
<style>
  :root {
    --bg: #f2f3f5;
    --paper: #ffffff;
    --yellow: #f7d417;
    --yellow-deep: #f5b800;
    --gold: #f2ac12;
    --charcoal: #4d4a4a;
    --charcoal-dark: #3d3a3a;
    --ink: #231f20;
    --white: #ffffff;
  }
  * { box-sizing: border-box; margin: 0; padding: 0; }
  html, body { width: 1200px; height: 1200px; overflow: hidden; background: var(--bg); }
  body { font-family: "Barlow", Arial, sans-serif; color: var(--ink); }
  .stage { position: absolute; left: 0; top: 0; width: 1500px; height: 1500px; transform: scale(0.8); transform-origin: 0 0; }
  .spread { position: absolute; background: var(--paper); overflow: hidden; box-shadow: 3px 4px 6px rgba(0,0,0,.35); }
  .spread--intro { left: 224px; top: 36px; width: 1054px; height: 686px; }
  .spread--brands { left: 228px; top: 785px; width: 1052px; height: 681px; }
  .spread-shapes { position: absolute; inset: 0; width: 100%; height: 100%; }
  .abs { position: absolute; }
  .section-title { font-style: italic; font-weight: 300; font-size: 33px; letter-spacing: .5px; white-space: nowrap; }
  .index-title { left: 44px; top: 42px; color: var(--white); letter-spacing: 3px; }
  .index-title .accent { color: var(--gold); margin-left: 14px; }
  .index-row { position: absolute; left: 69px; font-size: 12.5px; font-weight: 600; white-space: nowrap; }
  .index-row .page { color: var(--white); }
  .index-row .topic { position: absolute; top: 0; color: var(--gold); }
  .about-title { left: 551px; top: 92px; color: var(--charcoal); }
  .about-title .accent { color: var(--gold); }
  .about-copy { left: 551px; top: 163px; width: 178px; font-size: 10.2px; line-height: 13.6px; color: var(--ink); }
  .photo { position: absolute; inset: 0; }
  .page-no { font-style: italic; font-weight: 700; font-size: 13px; letter-spacing: .5px; }
  .brands-title { left: 30px; top: 34px; color: var(--gold); }
  .category-label { position: absolute; left: 38px; font-size: 12.5px; font-style: italic; font-weight: 700; color: var(--white); letter-spacing: 1.2px; }
  .brand-name { position: absolute; font-weight: 700; font-size: 21px; color: var(--charcoal-dark); white-space: nowrap; display: flex; align-items: center; gap: 8px; }
  .brand-name .mark { width: 18px; height: 18px; background: var(--gold); display: inline-block; }
  .brand-name--on-yellow { color: var(--ink); }
  .stock-title { left: 548px; top: 36px; color: var(--white); }
  .stock-lead { left: 597px; top: 125px; font-size: 12.5px; font-weight: 700; color: var(--white); }
  .stock-list { position: absolute; left: 616px; top: 168px; list-style: none; }
  .stock-list li { position: relative; padding-left: 20px; height: 34px; font-size: 12.5px; font-weight: 700; color: var(--white); letter-spacing: .3px; }
  .stock-list li::before { content: ""; position: absolute; left: 0; top: 5px; width: 7px; height: 7px; border-radius: 50%; background: var(--gold); }
</style>
</head>
<body>
<main class="stage">

  <section class="spread spread--intro">
    <svg class="spread-shapes" viewBox="0 0 1054 686" preserveAspectRatio="none" aria-hidden="true">
      <defs>
        <linearGradient id="yellowFade" x1="0" y1="0" x2="1" y2="1">
          <stop offset="0" stop-color="#f9d21a"/>
          <stop offset="1" stop-color="#f7e323"/>
        </linearGradient>
        <linearGradient id="charcoalFade" x1="0" y1="0" x2="1" y2="1">
          <stop offset="0" stop-color="#4a4646"/>
          <stop offset="1" stop-color="#5a5656"/>
        </linearGradient>
      </defs>
      <polygon points="0,0 100,0 426,686 0,686" fill="url(#yellowFade)"/>
      <polygon points="680,0 1054,0 1054,410 886,410" fill="url(#charcoalFade)"/>
      <polygon points="664,0 674,0 882,410 872,410" fill="var(--charcoal)"/>
    </svg>
    <svg class="photo" viewBox="0 0 1054 686" preserveAspectRatio="none" role="img" aria-label="Photo of three team members in black shirts standing in front of a large enclosed generator and an open diesel generator set">
      <defs>
        <linearGradient id="photoTone" x1="0" y1="0" x2="1" y2="1">
          <stop offset="0" stop-color="#e9e9ea"/>
          <stop offset=".55" stop-color="#8a8888"/>
          <stop offset="1" stop-color="#2b2a2a"/>
        </linearGradient>
      </defs>
      <polygon points="492,410 1054,410 1054,686 426,686" fill="url(#photoTone)"/>
    </svg>

    <h2 class="abs section-title index-title">INDE<span class="accent">X</span></h2>
    <div class="index-row" style="top:121px"><span class="page">PAGE 3 . . . . .</span><span class="topic" style="left:96px">ABOUT OUR COMPANY</span></div>
    <div class="index-row" style="top:155px"><span class="page">PAGE 4 . . . . . . . .</span><span class="topic" style="left:112px">OUR BRANDS</span></div>
    <div class="index-row" style="top:189px"><span class="page">PAGE 5 . . . . . . . . . .</span><span class="topic" style="left:128px">OUR STOCK</span></div>
    <div class="index-row" style="top:223px"><span class="page">PAGE 6 . . . . . . . . . . . .</span><span class="topic" style="left:144px">STANDBY GENERATORS</span></div>
    <div class="index-row" style="top:257px"><span class="page">PAGE 7 . . . . . . . . . . . . . .</span><span class="topic" style="left:161px">PRIME GENERATORS</span></div>
    <div class="index-row" style="top:291px"><span class="page">PAGE 8 . . . . . . . . . . . . . . . .</span><span class="topic" style="left:187px">AC ALTERNATORS</span></div>
    <div class="index-row" style="top:325px"><span class="page">PAGE 9 . . . . . . . . . . . . . . . . .</span><span class="topic" style="left:199px">RENTAL GENERATORS</span></div>
    <div class="index-row" style="top:359px"><span class="page">PAGE 10 . . . . . . . . . . . . . . . . . .</span><span class="topic" style="left:210px">ALTERNATOR PARTS</span></div>
    <div class="index-row" style="top:393px"><span class="page">PAGE 11 . . . . . . . . . . . . . . . . . . . .</span><span class="topic" style="left:226px">CONTROLLERS</span></div>
    <div class="index-row" style="top:427px"><span class="page">PAGE 12 . . . . . . . . . . . . . . . . . . . . . .</span><span class="topic" style="left:242px">TRANSFER SWITCHES</span></div>
    <div class="index-row" style="top:461px"><span class="page">PAGE 13 . . . . . . . . . . . . . . . . . . . . . . . .</span><span class="topic" style="left:258px">OUR DISTRIBUTORS</span></div>

    <h2 class="abs section-title about-title">ABOUT OUR <span class="accent">COMPANY</span></h2>
    <p class="abs about-copy">Not all customer needs are the same and being able to accommodate to the specifications of each can become challenging. Brightline Energy has the experience necessary to take on major special projects with a quick turn-around.<br>We understand the specific requirements of each industry and market. Our team of experts are capable modify and customized our products to fit your needs.<br>Let us worry about the complexities of manufacturing and engineering while you exploit the opportunity for your clients.</p>

    <span class="abs page-no" style="left:986px;top:640px;color:var(--white)">PAGE 3</span>
  </section>

  <section class="spread spread--brands">
    <svg class="spread-shapes" viewBox="0 0 1052 681" preserveAspectRatio="none" aria-hidden="true">
      <defs>
        <linearGradient id="yellowFade2" x1="0" y1="0" x2="1" y2="1">
          <stop offset="0" stop-color="#f9e21e"/>
          <stop offset="1" stop-color="#f7c40e"/>
        </linearGradient>
        <linearGradient id="charcoalFade2" x1="0" y1="0" x2="1" y2="1">
          <stop offset="0" stop-color="#4a4646"/>
          <stop offset="1" stop-color="#575353"/>
        </linearGradient>
      </defs>
      <polygon points="478,0 524,0 524,681 122,681" fill="url(#yellowFade2)"/>
      <rect x="524" y="0" width="528" height="681" fill="url(#charcoalFade2)"/>
      <polygon points="1052,150 1052,164 784,681 770,681" fill="var(--white)"/>
      <polygon points="1052,188 1052,681 792,681" fill="url(#yellowFade2)"/>
      <g fill="var(--charcoal)">
        <polygon points="28,86 415,86 405,106 28,106"/>
        <polygon points="28,192 360,192 350,212 28,212"/>
        <polygon points="28,298 304,298 294,318 28,318"/>
        <polygon points="28,404 248,404 238,424 28,424"/>
        <polygon points="28,511 192,511 182,531 28,531"/>
      </g>
    </svg>

    <h2 class="abs section-title brands-title">OUR BRANDS</h2>

    <span class="category-label" style="top:88px">DIESEL GENERATORS</span>
    <span class="brand-name" style="left:32px;top:134px"><span class="mark"></span>Brightline Energy</span>
    <span class="brand-name brand-name--on-yellow" style="left:416px;top:122px">Kestrel</span>
    <span class="brand-name brand-name--on-yellow" style="left:416px;top:146px">Norvane</span>

    <span class="category-label" style="top:194px">DIESEL GENERATORS</span>
    <span class="brand-name" style="left:29px;top:243px">Halvern Orvik</span>
    <span class="brand-name brand-name--on-yellow" style="left:354px;top:240px">Lumen Dorrel</span>

    <span class="category-label" style="top:300px">DIESEL GENERATORS</span>
    <span class="brand-name" style="left:29px;top:349px">Halvern Orvik</span>
    <span class="brand-name brand-name--on-yellow" style="left:298px;top:346px">Lumen Dorrel</span>

    <span class="category-label" style="top:406px">DIESEL GENERATORS</span>
    <span class="brand-name" style="left:36px;top:472px"><span class="mark"></span>Delvo</span>
    <span class="brand-name brand-name--on-yellow" style="left:232px;top:455px">Norvane</span>

    <span class="category-label" style="top:513px">DIESEL GENERATORS</span>
    <span class="brand-name" style="left:42px;top:560px">Arcline</span>
    <span class="brand-name brand-name--on-yellow" style="left:188px;top:562px;font-size:16px">Meridian · Tessary Power Systems</span>

    <span class="abs page-no" style="left:26px;top:636px;color:var(--charcoal)">PAGE 4</span>

    <h2 class="abs section-title stock-title">OUR STOCK</h2>
    <p class="abs stock-lead">OUR PRODUCTS ARE:</p>
    <ul class="stock-list">
      <li>DIESEL GENERATORS</li>
      <li>STANDBY GENERATORS</li>
      <li>PRIME GENERATORS</li>
      <li>RENTAL GENERATORS</li>
      <li>AC ALTERNATORS</li>
      <li>ALTERNATOR PARTS</li>
      <li>CONTROLLERS</li>
      <li>TRANSFER SWITCHES</li>
    </ul>

    <span class="abs page-no" style="left:971px;top:636px;color:var(--white)">PAGE 5</span>
  </section>

</main>
</body>
</html>
```